Bespoke Builders Business Card Design

We need a business card for an established builder of high quality bespoke homes in Auckland and Northland. We build and renovate homes collaboratively facilitating effective communication between owners, builders, architects, suppliers and tradespeople. We have never built or renovated a home that leaks or has faults. We only use reliable materials. We have never been sued or had legal action taken against us. We are honest builders of bespoke homes not group mass produced homes. Our niche market is in character homes. We practice sustainability and have built a lot of coastal property. We have been in business for over thirty years . We would like to see natural colors of the environment sand,sea and maybe vegetation . The design should communicate quality, sustainability,fair pricing, open communication and the originality of bespoke building. And the fact that the builder is registered.

Industry/Entity Type

Business

Contact Information for Business Card

Rowan Tellick Builders
Ph. 021583917
18 Kestrel Rd Harwood Bay Auckland 0814
PO Box 927 Mangawhai 0583

```html
<!DOCTYPE html>
<html lang="en">
<head>
<meta charset="utf-8">
<title>Rowan Tellick Builders – Business Card</title>
<link rel="stylesheet" href="https://fonts.googleapis.com/css2?family=Libre+Bodoni:wght@700&family=Source+Sans+3:wght@400&display=swap">
<style>
  :root {
    --navy: #2b2a72;
    --ink: #000000;
    --paper: #ffffff;
    --backdrop: #ebe8e4;
  }
  * { box-sizing: border-box; margin: 0; padding: 0; }
  html, body {
    width: 1189px;
    height: 1200px;
    overflow: hidden;
    background: var(--backdrop);
  }
  .card {
    position: absolute;
    left: 140px;
    width: 917px;
    height: 524px;
    overflow: hidden;
  }
  /* Front */
  .card--front {
    top: 45px;
    background: var(--paper);
  }
  .rule {
    position: absolute;
    left: 0;
    width: 100%;
    height: 2.5px;
    background: var(--ink);
  }
  .rule--top { top: 55px; }
  .rule--bottom { top: 164px; }
  .brand-name {
    font-family: "Libre Bodoni", "Bodoni Moda", serif;
    font-weight: 700;
    white-space: nowrap;
    text-align: center;
    letter-spacing: 0.5px;
  }
  .card--front .brand-name {
    position: absolute;
    top: 60px;
    left: 0;
    width: 100%;
    font-size: 62px;
    line-height: 100px;
    color: var(--navy);
  }
  .contact {
    position: absolute;
    top: 262px;
    left: 0;
    width: 100%;
    text-align: center;
    font-family: "Source Sans 3", "Myriad Pro", sans-serif;
    color: var(--ink);
  }
  .contact__phone {
    font-size: 29px;
    line-height: 40px;
    letter-spacing: 0.5px;
  }
  .contact__address {
    font-size: 29px;
    line-height: 40px;
    margin-top: 5px;
    letter-spacing: 0.3px;
  }
  .wave {
    position: absolute;
    left: 0;
    top: 0;
    width: 917px;
    height: 524px;
  }
  /* Back */
  .card--back {
    top: 624px;
    height: 522px;
    background: var(--ink);
    border: 14px solid var(--navy);
  }
  .card--back .brand-name {
    position: absolute;
    top: 212px;
    left: 0;
    width: 100%;
    font-size: 62px;
    line-height: 100px;
    color: var(--paper);
  }
</style>
</head>
<body>
  <section class="card card--front" aria-label="Business card front">
    <svg class="wave" viewBox="0 0 1124 642" preserveAspectRatio="none" aria-hidden="true">
      <path d="M0,524 C220,575 480,600 790,540 C560,592 300,610 0,568 Z" fill="var(--navy)"/>
      <path d="M0,578 C260,612 470,606 640,565 C780,530 880,505 960,512 C1030,518 1080,535 1124,565 L1124,642 L0,642 Z" fill="var(--ink)"/>
      <path d="M0,572 C260,606 470,600 640,559 C700,545 750,532 790,523" fill="none" stroke="var(--paper)" stroke-width="4"/>
    </svg>
    <div class="rule rule--top"></div>
    <h1 class="brand-name">Rowan Tellick Builders</h1>
    <div class="rule rule--bottom"></div>
    <address class="contact" style="font-style:normal">
      <p class="contact__phone">021583917</p>
      <p class="contact__address">18 Kestrel Rd Harwood Bay Auckland<br>0814 PO Box 927 Mangawhai 0583</p>
    </address>
  </section>

  <section class="card card--back" aria-label="Business card back">
    <p class="brand-name">Rowan Tellick Builders</p>
  </section>
</body>
</html>
```